Business cards in digital learning for freelancer

Hello, I need a business cards in french. I work in the Digital learning industries as freeelancer; I'm an expert in digital learning. I work in France. My customer are in the health industry, pharmaceutical industry, and training organization. I've got a logo. I offer three services: consulting, Design, and Training. In the consulting, I offers coaching to choose your digital learning tools and the digital learning strategy. For the Design, I product differents level of elearning like rapid-learning, elearning, micro-learning, video-learning. And for the training service, I've create training about pedagogy, digital learning management project, Digital learning design.
I join my Logo create in this platform. My universe is gamified. I like the life, and I'm very social. I want a card like I'm I. I love Art (painting), Europeen comics. I use in my visual support "permanent maker" font and caracters. I would like cards: elegant, modern, Top class. If you need any information, you can ask me.
thanks for ideas

Target Market(s)

in health industries and training organization for Training manager, instructor, human resources director

Contact Information for Business Card

Phone number : 06 71 38 95 14 , mail: bastiengolmier@quelmoto.fr, web: bastiengolmier.fr , Carrivo

Font styles to use
Sans Serif

Requirements
Must have
• Use my logo and write my 3 services (consulting, training, design)

```html
<!DOCTYPE html>
<html lang="fr">
<head>
<meta charset="utf-8">
<title>Golmier – cartes de visite</title>
<link rel="stylesheet" href="https://fonts.googleapis.com/css2?family=Cinzel:wght@400;600&family=Josefin+Sans:wght@300;400;700&display=swap">
<style>
  :root {
    --orange: #d9692a;
    --grey: #747474;
    --grey-dark: #5f5f5f;
    --paper: #f7f7f5;
    --backdrop: #e6e6e4;
    --white: #ffffff;
  }
  * { box-sizing: border-box; margin: 0; padding: 0; }
  html, body {
    width: 1200px; height: 801px; overflow: hidden;
    background: var(--backdrop);
  }
  .stage {
    width: 1200px; height: 801px;
    display: flex; align-items: center; justify-content: center; gap: 40px;
  }
  .card {
    position: relative;
    width: 540px; height: 348px;
    overflow: hidden;
    box-shadow: 0 6px 18px rgba(0,0,0,.14);
  }
  .card--front { background: var(--paper); }
  .card--back {
    background: var(--orange);
    display: flex; flex-direction: column; align-items: center; justify-content: center;
  }

  /* front */
  .illustration {
    position: absolute; left: 0; bottom: 0;
    width: 250px; height: 270px;
    border-top-right-radius: 140px;
    background: linear-gradient(160deg, var(--orange) 0%, #e2905f 55%, var(--grey) 100%);
  }
  .identity {
    position: absolute; right: 30px; top: 30px;
    text-align: right;
  }
  .wordmark {
    font-family: "Josefin Sans", sans-serif; font-weight: 700;
    color: var(--orange); font-size: 44px; letter-spacing: 3px; line-height: 1;
  }
  .tagline {
    font-family: "Cinzel", serif; color: var(--grey-dark);
    font-size: 13px; letter-spacing: 1px; line-height: 1.5;
  }
  .tagline--field { border-top: 1px solid var(--grey); margin-top: 6px; padding-top: 3px; }
  .contact {
    position: absolute; right: 30px; bottom: 32px;
    text-align: right;
    font-family: "Josefin Sans", sans-serif;
  }
  .contact__name { color: var(--orange); font-size: 22px; font-weight: 400; }
  .contact__role { color: var(--grey); font-size: 14px; font-weight: 300; margin-bottom: 12px; }
  .contact__list { list-style: none; }
  .contact__item {
    display: flex; align-items: center; justify-content: flex-end; gap: 8px;
    color: var(--grey); font-size: 13px; font-weight: 300; line-height: 21px;
  }
  .contact__icon { width: 16px; height: 16px; flex: none; }

  /* back */
  .back__mark {
    display: flex; align-items: center; gap: 14px;
  }
  .back__dot { width: 22px; height: 22px; border-radius: 50%; background: var(--white); }
  .back__wordmark {
    font-family: "Josefin Sans", sans-serif; font-weight: 700;
    color: var(--white); font-size: 56px; letter-spacing: 4px; line-height: 1;
  }
  .back__tagline {
    font-family: "Cinzel", serif; color: var(--white);
    font-size: 16px; letter-spacing: 1.5px; margin-top: 10px;
  }
</style>
</head>
<body>
<main class="stage">
  <section class="card card--front">
    <div class="illustration" role="img" aria-label="Illustration d'arbre stylisé aux branches orange et grises dans un grand arc orange"></div>

    <header class="identity">
      <div class="wordmark">GOLMIER</div>
      <p class="tagline tagline--field">Digital Learning</p>
      <p class="tagline">Consulting, Training, Design</p>
    </header>

    <div class="contact">
      <p class="contact__name">Bastien Golmier</p>
      <p class="contact__role">Digital Learning consultant</p>
      <ul class="contact__list">
        <li class="contact__item">06 71 38 95 14
          <svg class="contact__icon" viewBox="0 0 16 16"><circle cx="8" cy="8" r="8" fill="var(--orange)"/><path d="M5 4.5l1.5-.5 1 2-1 .8a5 5 0 0 0 2.7 2.7l.8-1 2 1-.5 1.5c-3.5.2-6.7-3-6.5-6.5z" fill="#fff"/></svg>
        </li>
        <li class="contact__item">bastiengolmier@quelmoto.fr
          <svg class="contact__icon" viewBox="0 0 16 16"><circle cx="8" cy="8" r="8" fill="var(--orange)"/><rect x="4" y="5" width="8" height="6" fill="#fff"/><path d="M4 5l4 3.3L12 5" fill="none" stroke="var(--orange)" stroke-width=".9"/></svg>
        </li>
        <li class="contact__item">bastiengolmier.fr
          <svg class="contact__icon" viewBox="0 0 16 16"><circle cx="8" cy="8" r="8" fill="var(--orange)"/><circle cx="8" cy="8" r="4" fill="none" stroke="#fff" stroke-width="1"/><path d="M4 8h8M8 4c-2 2.5-2 5.5 0 8M8 4c2 2.5 2 5.5 0 8" fill="none" stroke="#fff" stroke-width=".8"/></svg>
        </li>
        <li class="contact__item">/carrivo/bastien-golmier
          <svg class="contact__icon" viewBox="0 0 16 16"><circle cx="8" cy="8" r="8" fill="var(--orange)"/></svg>
        </li>
      </ul>
    </div>
  </section>

  <section class="card card--back">
    <div class="back__mark">
      <span class="back__dot"></span>
      <span class="back__wordmark">GOLMIER</span>
    </div>
    <p class="back__tagline">Consulting, Training, Design</p>
  </section>
</main>
</body>
</html>
```